Tax Preparation flyer for LedgerVale Corp.

My Client would like a one page PDF flyer to promote upcoming tax season in Canada. This firm is affordable and all virtual. I have attached a copy of their logo and a word document with the proposed wording for the flyer. Please feel free to change if you have better suggestions.

Target Market(s)

individuals in canada

Colors
0054AA
0677BA
7BADD7
CADEEF
E8F1F8

```html
<!DOCTYPE html>
<html lang="en">
<head>
<meta charset="utf-8">
<title>LedgerVale Corp. – Tax Season Flyer</title>
<link rel="stylesheet" href="https://fonts.googleapis.com/css2?family=Poppins:ital,wght@0,400;0,500;0,600;0,700;0,800;1,600;1,700&family=Oswald:wght@500;600&display=swap">
<style>
  :root{
    --navy:#0054AA;
    --blue:#0677BA;
    --bright:#2a8fe0;
    --sky:#7BADD7;
    --mist:#CADEEF;
    --ice:#E8F1F8;
    --ink:#1f2124;
    --ink-2:#2b2e33;
    --cell:#3a3d42;
    --white:#ffffff;
    --red:#e3141b;
    --stage:#e9ebee;
  }
  *{box-sizing:border-box;margin:0;padding:0}
  html,body{width:1200px;height:2400px;overflow:hidden;background:var(--stage)}
  body{font-family:"Poppins",sans-serif;color:var(--white);position:relative}

  .flyer{position:absolute;left:0;top:423px;width:1200px;height:1553px;
    background:radial-gradient(ellipse at 60% 85%,#34373c 0%,var(--ink) 60%);overflow:hidden}
  .abs{position:absolute}

  .brand{left:72px;top:62px;font-weight:700;font-size:58px;line-height:1;color:var(--white);letter-spacing:-1px}

  .hero-photo{left:562px;top:6px;width:638px;height:515px;
    background:radial-gradient(circle at 30% 40%,rgba(227,20,27,.85) 0 28%,transparent 29%),
               radial-gradient(ellipse at 62% 60%,var(--bright) 0 32%,transparent 55%),
               linear-gradient(160deg,#3a3530,#23262a);
    border-radius:4px}

  .headline{left:74px;top:272px}
  .headline .relax{font-weight:800;font-size:98px;color:var(--bright);line-height:1;letter-spacing:1px}
  .headline .line2{font-weight:500;font-size:60px;line-height:1.05;margin-top:12px}
  .headline .line3{font-weight:800;font-size:64px;line-height:1.05}

  .intro-band{left:77px;top:553px;width:1036px;height:180px;display:flex}
  .intro-left{width:518px;background:linear-gradient(90deg,#0a5fa8,var(--blue));display:flex;align-items:center;padding:0 14px 0 16px;gap:12px}
  .intro-right{flex:1;background:linear-gradient(90deg,#1186d0,#1a8ed8);padding:16px 18px 0 20px}
  .years{font-family:"Oswald",sans-serif;text-align:center;line-height:.95}
  .years .num{font-size:84px;font-weight:600}
  .years .lbl{font-size:19px;font-weight:500}
  .intro-left p{font-size:15.5px;line-height:1.22}
  .intro-right p{font-size:15.5px;line-height:1.22}
  .intro-right .strong{font-weight:600;font-size:15.5px;line-height:1.22}
  .meet-row{display:flex;align-items:center;justify-content:space-between;margin-top:14px}
  .partner{display:flex;align-items:center;gap:8px;font-weight:600;font-size:18px}
  .partner .sq{width:26px;height:26px;background:var(--mist);border-radius:4px}
  .sign{font-weight:600}

  .pricing-tag{left:84px;top:803px;width:36px;height:206px;background:var(--white);border-radius:3px}
  .pricing-tag span{position:absolute;left:50%;top:50%;transform:translate(-50%,-50%) rotate(-90deg);
    color:var(--ink);font-weight:700;font-size:26px;letter-spacing:5px}
  .price{left:150px;top:812px}
  .price .title{color:var(--bright);font-weight:600;font-size:33px;line-height:1}
  .price .main{font-weight:700;font-size:82px;line-height:1;margin-top:4px;letter-spacing:-1px}
  .price .add{font-size:21px;font-weight:400;letter-spacing:.3px;margin-top:4px}
  .price .second{display:flex;align-items:center;gap:6px;margin-top:2px}
  .price .second b{color:var(--bright);font-size:72px;font-weight:700;line-height:1}
  .price .second em{font-style:normal;background:var(--white);color:var(--ink);font-weight:700;font-size:19px;line-height:1.05;padding:5px 12px;border-radius:3px}

  .details{left:612px;top:800px;width:510px;font-size:15.5px;line-height:1.25}
  .details p{margin-bottom:16px}
  .details .cta{color:var(--bright);font-weight:600;font-size:17px}

  .bk-illustration{left:66px;top:1055px;width:180px;height:200px;
    background:linear-gradient(150deg,var(--sky),var(--blue) 60%,var(--navy));border-radius:10px;opacity:.9}
  .autopilot{left:289px;top:1096px;width:190px;color:var(--bright);font-weight:600;font-style:italic;font-size:17.5px;line-height:1.2}
  .clients{left:72px;top:1278px;width:400px;font-size:14.5px;line-height:1.22}
  .clients .lead{font-weight:600;font-size:17.5px;margin-bottom:8px}
  .clients b{font-weight:600}
  .clients p{margin-bottom:14px}

  .costs{left:498px;top:1079px;width:622px}
  .costs-head{height:59px;background:var(--blue);border-radius:6px 6px 0 0;display:flex;align-items:center;justify-content:center;
    font-weight:600;font-size:18px;letter-spacing:5px}
  .costs-grid{display:grid;grid-template-columns:repeat(4,1fr);gap:4px;margin-top:8px}
  .costs-grid .hd{background:var(--blue);height:52px;display:flex;align-items:center;justify-content:center;text-align:center;font-size:17px;line-height:1.1}
  .costs-grid .hd.dark{background:var(--navy)}
  .costs-grid .cell{background:var(--cell);height:100px;display:flex;align-items:center;justify-content:center;text-align:center;font-size:17px;line-height:1.2}
  sup{font-size:10px}

  .call{left:500px;top:1346px;color:var(--bright);font-weight:700;font-size:36px;letter-spacing:6px}
  .contact{top:1399px;display:flex;align-items:center;gap:8px;font-weight:500;font-size:22px}
  .phone{left:505px}
  .mail{left:793px}
  .contact svg{width:20px;height:20px}
  .web{left:500px;top:1432px;width:620px;height:55px;background:var(--bright);border-radius:6px;
    display:flex;align-items:center;justify-content:center;font-weight:600;font-size:30px;letter-spacing:8px}
</style>
</head>
<body>
<main class="flyer">
  <div class="abs brand">LedgerVale Corp.</div>

  <div class="abs hero-photo" role="img" aria-label="Smiling woman in a blue sweater and white sunglasses holding a fan of banknotes in front of a red maple leaf, with bills flying around"></div>

  <h1 class="abs headline">
    <div class="relax">RELAX,</div>
    <div class="line2">WE’VE GOT YOUR</div>
    <div class="line3">TAXES COVERED!</div>
  </h1>

  <section class="abs intro-band">
    <div class="intro-left">
      <div class="years"><div class="num">20</div><div class="lbl">YEARS OF<br>EXPERIENCE</div></div>
      <p>Our tax preparers have over worked both in public accounting firms as well as specialized tax. Our tax services are virtual, so you don’t have to take the time for a personal visit. We take care of everything and can access all your tax slips from CRA website directly into our tax software. All signing is done via <span class="sign">SignPoint</span></p>
    </div>
    <div class="intro-right">
      <p>You can fill and submit the appropriate forms, along with all your other documents, in our secure client portal. It’s important that we understand your situation and any changes in your situation from the past year.</p>
      <div class="meet-row">
        <p class="strong">If you have a complex tax situation<br>and would like to discuss it, we can<br>meet in virtually over MeetLine or TalkRoom</p>
        <div class="partner"><span class="sq"></span>MeetLine</div>
      </div>
    </div>
  </section>

  <div class="abs pricing-tag"><span>PRICING</span></div>
  <section class="abs price">
    <div class="title">PERSONAL TAX RETURN</div>
    <div class="main">$100.00</div>
    <div class="add">ADD A BUSINESS OR RENTAL SCHEDULE</div>
    <div class="second"><b>$125</b><em>PER BUSINESS OR<br>RENTAL PROPERTY</em></div>
  </section>

  <section class="abs details">
    <p>More complex tax returns will be assessed based on the complexity of the return and you will be advised before we start.</p>
    <p>Did you fall behind in filing your income tax save 20% when you file 3 or more years with us. We can do back to 2012 for filing of tax returns.</p>
    <p>If you expect a refund, the earlier you file the sooner you will receive your refund. Our average turn around time prior to April is a couple of days.<br><span class="cta">TODAY SO YOU CAN START TO BREATHE EASY.</span></p>
  </section>

  <div class="abs bk-illustration" role="img" aria-label="Isometric illustration of a laptop with charts, documents and coins"></div>
  <p class="abs autopilot">Imagine having your bookkeeping on auto pilot, with everything always up to date and available at your fingertips. Anytime. Anywhere.</p>

  <section class="abs clients">
    <p class="lead">You’ll always know exactly where you stand with your cash flow—how much you have, owe, are owed, and have made.</p>
    <p><b>How will you feel?</b><br>Calm, relaxed, and able to make good business decisions. And you’ll have more time to work on your business. In short, you’ll be able to breathe easy.</p>
    <p><b>Sound too good to be true?</b><br>That’s exactly how our clients feel once all their bookkeeping stresses are gone.</p>
  </section>

  <section class="abs costs">
    <div class="costs-head">BOOKKEEPING &amp; ACCOUNTING COSTS</div>
    <div class="costs-grid">
      <div class="hd">DIY</div>
      <div class="hd dark">Part-Time<br>Bookkeeper</div>
      <div class="hd dark">Full-Time<br>Bookkeeper</div>
      <div class="hd dark">FullOutsources<br>Accounting Team</div>
      <div class="cell">No added<br>financial<br>cost</div>
      <div class="cell">$3,500-4,500<br>Per month +<br>benefits<sup>(1)</sup></div>
      <div class="cell">$4,800-5,500<br>Per month +<br>benefits<sup>(2)</sup></div>
      <div class="cell">$5,000+<sup>(4)</sup></div>
    </div>
  </section>

  <div class="abs call">CALL US TODAY!</div>
  <div class="abs contact phone">
    <svg viewBox="0 0 20 20"><circle cx="10" cy="10" r="10" fill="var(--bright)"/><path d="M6.5 5.5l2 2-1 1.3c.7 1.5 1.7 2.5 3.2 3.2l1.3-1 2 2-1.2 1.5C9.5 14.3 5.7 10.5 5 7z" fill="#fff"/></svg>
    555 0142 0199
  </div>
  <div class="abs contact mail">
    <svg viewBox="0 0 20 20"><circle cx="10" cy="10" r="10" fill="var(--bright)"/><rect x="5" y="6.5" width="10" height="7" rx="1" fill="#fff"/><path d="M5.3 7l4.7 3.5L14.7 7" stroke="var(--bright)" stroke-width="1.2" fill="none"/></svg>
    info@Ledgervalecorp.com
  </div>
  <div class="abs web">www.Ledgervalecorp.com</div>
</main>
</body>
</html>
```